Coffeeshop menu for filter tip

We want to have a cannabis (coffeeshop) menu in the size 25mm wide x 60mm wide. Some examples attached.

it must have the following text:
Menu

WEED p/g
Oblivane €16
Cloudplum €14
Tide Runner €14
Quincefig €16
Mega Marsh €14
Grey Heron €14

HASH p/g
Tashar Amber €12
Pebble Frost€11
Lime Dunes €14
Ash Petal €10

Target Market(s)

tourist in Amsterdam

Requirements
Nice to have
• cannabis sign leaf
• No Cigarettes allowed symbol

```html
<!DOCTYPE html>
<html lang="en">
<head>
<meta charset="utf-8">
<title>Amsterdam Menu</title>
<link rel="stylesheet" href="https://fonts.googleapis.com/css2?family=Anton&family=Kaushan+Script&family=Montserrat:wght@400&family=Play:wght@400&family=Yellowtail&display=swap">
<style>
  :root {
    --bg-deep: #163a1e;
    --bg-mid: #1f4d27;
    --bg-light: #27622f;
    --bg-dark: #13241a;
    --cream: #efeedb;
    --yellow: #f6ef7c;
    --white: #ffffff;
    --ring: #1b4a22;
    --leaf-light: #8cc63f;
    --leaf-dark: #2f8a2f;
    --no-red: #e0232b;
  }
  html, body {
    margin: 0;
    padding: 0;
    width: 1200px;
    height: 2878px;
    overflow: hidden;
  }
  .menu {
    position: relative;
    width: 1200px;
    height: 2878px;
    overflow: hidden;
    background: linear-gradient(160deg, var(--bg-mid) 0%, var(--bg-deep) 35%, var(--bg-light) 55%, var(--bg-deep) 75%, var(--bg-dark) 100%);
    font-family: "Play", sans-serif;
    color: var(--cream);
  }
  .menu__frame {
    position: absolute;
    inset: 0;
  }
  .menu__badge {
    position: absolute;
    left: 410px;
    top: 108px;
    width: 380px;
    height: 380px;
  }
  .menu__city {
    position: absolute;
    left: 0;
    width: 1200px;
    top: 478px;
    text-align: center;
    font-family: "Kaushan Script", cursive;
    font-size: 104px;
    line-height: 1;
    color: var(--yellow);
  }
  .menu__title {
    position: absolute;
    left: 0;
    width: 1200px;
    top: 566px;
    text-align: center;
    font-family: "Anton", sans-serif;
    font-size: 236px;
    line-height: 1;
    color: var(--white);
    margin: 0;
    font-weight: 400;
  }
  .section {
    position: absolute;
    left: 241px;
    width: 733px;
  }
  .section--weed { top: 820px; }
  .section--hash { top: 1850px; }
  .section__head {
    position: relative;
    height: 196px;
  }
  .section--hash .section__head { height: 216px; }
  .section__name {
    position: absolute;
    left: -8px;
    bottom: 4px;
    margin: 0;
    font-family: "Yellowtail", cursive;
    font-weight: 400;
    font-size: 210px;
    line-height: 1;
    color: var(--yellow);
  }
  .section__unit {
    position: absolute;
    left: 591px;
    bottom: 24px;
    font-size: 64px;
    line-height: 1;
    color: var(--cream);
  }
  .price-list {
    list-style: none;
    margin: 0;
    padding: 0;
  }
  .price-list__item {
    position: relative;
    display: flex;
    align-items: center;
    justify-content: space-between;
    height: 126.4px;
    padding: 0 20px 0 18px;
    box-sizing: border-box;
    font-size: 68px;
    border-bottom: 2px solid var(--cream);
  }
  .price-list__item::before,
  .price-list__item::after {
    content: "";
    position: absolute;
    bottom: -4px;
    width: 6px;
    height: 6px;
    border-radius: 50%;
    background: var(--cream);
  }
  .price-list__item::before { left: 0; }
  .price-list__item::after { right: 0; }
  .price-list__name { color: var(--cream); }
  .price-list__price { color: var(--yellow); }
  .notice {
    position: absolute;
    left: 348px;
    top: 2656px;
    display: flex;
    align-items: center;
    gap: 20px;
  }
  .notice__text {
    font-family: "Montserrat", sans-serif;
    font-size: 50px;
    color: var(--white);
    letter-spacing: 0;
  }
</style>
</head>
<body>
<main class="menu">
  <svg class="menu__frame" width="1200" height="2878" viewBox="0 0 1200 2878" aria-hidden="true">
    <path d="M100 45 H1102 A60 60 0 0 0 1162 105 V2772 A60 60 0 0 0 1102 2832 H100 A60 60 0 0 0 40 2772 V105 A60 60 0 0 0 100 45 Z" fill="none" stroke="var(--cream)" stroke-width="7"/>
    <path d="M104 61 H1098 A48 48 0 0 0 1146 109 V2768 A48 48 0 0 0 1098 2816 H104 A48 48 0 0 0 56 2768 V109 A48 48 0 0 0 104 61 Z" fill="none" stroke="var(--cream)" stroke-width="3"/>
  </svg>

  <svg class="menu__badge" viewBox="0 0 380 380">
    <defs>
      <radialGradient id="leafTone" cx="50%" cy="45%" r="55%">
        <stop offset="0%" stop-color="var(--leaf-light)"/>
        <stop offset="100%" stop-color="var(--leaf-dark)"/>
      </radialGradient>
    </defs>
    <circle cx="190" cy="190" r="188" fill="var(--white)"/>
    <circle cx="190" cy="190" r="166" fill="none" stroke="var(--ring)" stroke-width="12"/>
    <circle cx="190" cy="186" r="128" fill="url(#leafTone)" opacity="0.85" role="img" aria-label="Green cannabis leaf illustration"/>
  </svg>

  <div class="menu__city">Amsterdam</div>
  <h1 class="menu__title">MENU</h1>

  <section class="section section--weed">
    <div class="section__head">
      <h2 class="section__name">Weed</h2>
      <span class="section__unit">p/g</span>
    </div>
    <ul class="price-list">
      <li class="price-list__item"><span class="price-list__name">Oblivane</span><span class="price-list__price">€16</span></li>
      <li class="price-list__item"><span class="price-list__name">Cloudplum</span><span class="price-list__price">€14</span></li>
      <li class="price-list__item"><span class="price-list__name">Tide Runner</span><span class="price-list__price">€14</span></li>
      <li class="price-list__item"><span class="price-list__name">Quincefig</span><span class="price-list__price">€16</span></li>
      <li class="price-list__item"><span class="price-list__name">Mega Marsh</span><span class="price-list__price">€14</span></li>
      <li class="price-list__item"><span class="price-list__name">Grey Heron</span><span class="price-list__price">€14</span></li>
    </ul>
  </section>

  <section class="section section--hash">
    <div class="section__head">
      <h2 class="section__name">Hash</h2>
      <span class="section__unit">p/g</span>
    </div>
    <ul class="price-list">
      <li class="price-list__item"><span class="price-list__name">Tashar Amber</span><span class="price-list__price">€12</span></li>
      <li class="price-list__item"><span class="price-list__name">Pebble Frost</span><span class="price-list__price">€11</span></li>
      <li class="price-list__item"><span class="price-list__name">Lime Dunes</span><span class="price-list__price">€14</span></li>
      <li class="price-list__item"><span class="price-list__name">Ash Petal</span><span class="price-list__price">€10</span></li>
    </ul>
  </section>

  <div class="notice">
    <svg width="102" height="102" viewBox="0 0 102 102" aria-hidden="true">
      <circle cx="51" cy="51" r="46" fill="var(--white)" stroke="var(--no-red)" stroke-width="9"/>
      <rect x="22" y="56" width="52" height="10" fill="var(--bg-deep)"/>
      <rect x="76" y="56" width="5" height="10" fill="var(--bg-deep)"/>
      <path d="M30 52 C26 44 36 42 32 34" fill="none" stroke="var(--bg-deep)" stroke-width="3"/>
      <line x1="20" y1="20" x2="82" y2="82" stroke="var(--no-red)" stroke-width="9"/>
    </svg>
    <span class="notice__text">NO CIGARETTES</span>
  </div>
</main>
</body>
</html>
```